Modern Business Card For A Digital Advertising Company

I'll be print on the Pell Prints Velour paper http://us.pellprints.com/products/velour/business-cards.html
Need's to be modern and use the color palette of the logo or gray scales. I think integrating the pixelation of the logo in to the card and having it wrap from one side to the other could be interesting. My company provides ad operations, web development, and number of other services to websites around the world. You can see my website at http://www.zantorhq.com
Contact info on the card needs to have
Owen Lasko
President
p.318.204.6637
owen@zantorhq.com
http://www.zantorhq.com
Doesn't necessarily need to be in that order
Website owners
Business

```html
<!DOCTYPE html>
<html lang="en">
<head>
<meta charset="utf-8">
<title>Zantor — Business Card</title>
<link rel="stylesheet" href="https://fonts.googleapis.com/css2?family=Open+Sans:wght@600;700;800&family=Tinos:wght@400;700&display=swap">
<style>
  :root {
    --backdrop: #1f1f1f;
    --white: #ffffff;
    --green-light: #8cc63f;
    --green-mid: #74ad36;
    --green-dark: #5a8f2c;
    --green-pale: #c9e3a6;
    --charcoal: #3a3a3a;
  }
  * { margin: 0; padding: 0; box-sizing: border-box; }
  html, body {
    width: 1200px; height: 757px; overflow: hidden;
    background: var(--backdrop);
  }
  .canvas { position: relative; width: 1200px; height: 757px; }
  .card {
    position: absolute; top: 228px;
    width: 520px; height: 300px;
    border-radius: 24px; overflow: hidden;
    box-shadow: 0 12px 30px rgba(0,0,0,0.55);
  }
  .card-front { left: 50px; }
  .card-back {
    left: 630px;
    background: linear-gradient(160deg, var(--green-dark) 0%, var(--green-mid) 55%, var(--green-light) 100%);
  }
  .card-art { position: absolute; inset: 0; width: 100%; height: 100%; }

  .brand {
    position: absolute; left: 40px; top: 38px;
    display: flex; align-items: center; gap: 12px;
  }
  .brand-mark { width: 22px; height: 22px; background: var(--green-light); }
  .brand-name {
    font-family: "Open Sans", sans-serif; font-weight: 800;
    font-size: 34px; letter-spacing: 2px; color: var(--green-mid);
  }

  .contact {
    position: absolute; right: 30px; top: 180px;
    list-style: none;
    font-family: "Tinos", serif; font-size: 15px; line-height: 1; color: var(--white);
  }
  .contact li {
    display: flex; justify-content: flex-end; align-items: center;
    gap: 6px; margin-bottom: 8px;
  }
  .contact svg { width: 11px; height: 11px; fill: var(--white); flex: none; }

  .person {
    position: absolute; left: 40px; bottom: 26px;
    font-family: "Tinos", serif; color: var(--white);
  }
  .person-name { font-size: 22px; font-weight: 700; line-height: 1.1; }
  .person-title { font-size: 15px; line-height: 1.1; margin-left: 52px; }

  .back-brand {
    position: absolute; left: 0; right: 0; top: 92px;
    display: flex; justify-content: center; align-items: center; gap: 14px;
  }
  .back-brand .brand-mark { width: 30px; height: 30px; background: var(--white); }
  .back-brand .brand-name { font-size: 60px; color: var(--white); letter-spacing: 4px; }
  .back-url {
    position: absolute; left: 0; right: 0; bottom: 44px; text-align: center;
    font-family: "Open Sans", sans-serif; font-weight: 700; font-size: 19px;
    letter-spacing: 1px; color: var(--white);
  }
</style>
</head>
<body>
<main class="canvas">

  <section class="card card-front" aria-label="Card front">
    <svg class="card-art" viewBox="0 0 520 300" preserveAspectRatio="none" aria-hidden="true">
      <defs>
        <linearGradient id="wave-green" x1="0" y1="0" x2="1" y2="1">
          <stop offset="0" stop-color="#86c13c"/>
          <stop offset="1" stop-color="#5e952d"/>
        </linearGradient>
      </defs>
      <rect width="520" height="300" fill="#ffffff"/>
      <path d="M0 110 C70 175 160 195 260 168 S440 95 520 80 L520 300 L0 300 Z" fill="#c9e3a6"/>
      <path d="M0 118 C70 183 160 203 260 176 S440 103 520 88 L520 300 L0 300 Z" fill="#3a3a3a"/>
      <path d="M0 124 C70 189 160 209 260 182 S440 109 520 94 L520 300 L0 300 Z" fill="#ffffff"/>
      <path d="M0 128 C70 193 160 213 260 186 S440 113 520 98 L520 300 L0 300 Z" fill="url(#wave-green)"/>
    </svg>

    <div class="brand">
      <span class="brand-mark"></span>
      <span class="brand-name">ZANTOR</span>
    </div>

    <ul class="contact">
      <li>
        <svg viewBox="0 0 24 24"><path d="M6.6 10.8a15.1 15.1 0 0 0 6.6 6.6l2.2-2.2a1 1 0 0 1 1-.25 11.4 11.4 0 0 0 3.6.57 1 1 0 0 1 1 1V20a1 1 0 0 1-1 1A17 17 0 0 1 3 4a1 1 0 0 1 1-1h3.5a1 1 0 0 1 1 1c0 1.25.2 2.45.57 3.57a1 1 0 0 1-.25 1z"/></svg>
        318.204.6637
      </li>
      <li>
        <svg viewBox="0 0 24 24"><path d="M2 5h20v14H2z M4 7l8 6 8-6" fill="none" stroke="#fff" stroke-width="2.5"/></svg>
        owen@zantorhq.com
      </li>
      <li>
        <svg viewBox="0 0 24 24"><circle cx="12" cy="12" r="10"/></svg>
        www.zantorhq.com
      </li>
    </ul>

    <div class="person">
      <p class="person-name">Owen Lasko</p>
      <p class="person-title">President</p>
    </div>
  </section>

  <section class="card card-back" aria-label="Card back">
    <div class="back-brand">
      <span class="brand-mark"></span>
      <span class="brand-name">ZANTOR</span>
    </div>
    <p class="back-url">www.zantorhq.com</p>
  </section>

</main>
</body>
</html>
```